Personal training and nutrition business needs business card design

We need a business card that outlays our services and invites potential customers to join our team and take the first step to a healthier and more enjoyable life. We cater for any level of fitness and specialize in weight loss and conditioning, strength training, muscle gain and strength endurance. Whether you are just starting off or need some help getting to the next level of your journey we are here to get the job done.
We specialize in one on one or one on two personal training sessions and each program will be custom made to suit individual fitness goals of our clients

```html
<!DOCTYPE html>
<html lang="en">
<head>
<meta charset="utf-8">
<title>Stride &amp; Core — Business Card</title>
<link rel="stylesheet" href="https://fonts.googleapis.com/css2?family=Arimo:wght@400;700&family=Oswald:wght@400&display=swap">
<style>
  :root {
    --bg: #1c1c1d;
    --card: #0b0b0c;
    --card-edge: #1a1a1b;
    --purple: #9b5bd6;
    --purple-light: #c57fd9;
    --white: #f2f2f2;
    --grey: #c9c9c9;
    --divider: #2a2a2c;
  }
  * { box-sizing: border-box; margin: 0; padding: 0; }
  html, body { width: 1200px; height: 900px; overflow: hidden; }
  body {
    background: var(--bg);
    font-family: "Arimo", Arial, sans-serif;
    color: var(--white);
    display: flex;
    flex-direction: column;
    align-items: center;
    justify-content: center;
    gap: 34px;
  }
  .card {
    width: 700px;
    height: 400px;
    background: var(--card);
    border: 1px solid var(--card-edge);
    border-radius: 26px;
    position: relative;
    overflow: hidden;
  }

  /* Front */
  .card-front { display: flex; }
  .brand-panel {
    width: 330px;
    border-right: 1px solid var(--divider);
    display: flex;
    flex-direction: column;
    align-items: center;
    justify-content: center;
    gap: 16px;
  }
  .brand-mark {
    width: 86px; height: 86px;
    border-radius: 50%;
    background: linear-gradient(135deg, var(--purple), var(--purple-light));
  }
  .brand-name {
    font-weight: 700;
    font-size: 40px;
    letter-spacing: 1px;
    text-transform: uppercase;
    color: var(--white);
    line-height: 1;
    text-align: center;
  }
  .brand-tagline {
    font-family: "Oswald", "Arial Narrow", sans-serif;
    font-size: 12px;
    letter-spacing: 1.6px;
    text-transform: uppercase;
    color: var(--purple);
  }
  .contact-panel {
    flex: 1;
    padding: 76px 0 0 44px;
  }
  .person-name {
    font-size: 27px;
    color: var(--purple);
    text-transform: uppercase;
    letter-spacing: 0.5px;
  }
  .person-role { font-size: 19px; color: var(--grey); margin-top: 4px; }
  .contact-list { list-style: none; margin-top: 22px; }
  .contact-list li {
    display: flex; align-items: center; gap: 10px;
    font-size: 20px; color: var(--white);
    margin-bottom: 7px;
  }
  .contact-list svg { width: 18px; height: 18px; flex: none; }
  .contact-list .accent { color: var(--purple); }
  .address { margin-top: 20px; font-size: 20px; color: var(--grey); line-height: 1.3; padding-left: 28px; }

  /* Back */
  .card-back {
    display: flex;
    flex-direction: column;
    align-items: center;
    justify-content: center;
  }
  .back-brand { display: flex; align-items: center; gap: 22px; }
  .back-brand .brand-mark {
    width: 92px; height: 92px;
    background: linear-gradient(135deg, #ffffff, #8f8f8f);
  }
  .back-brand .brand-text { display: flex; flex-direction: column; gap: 8px; }
  .back-brand .brand-name { font-size: 48px; text-align: left; color: #d4d4d4; }
  .back-brand .brand-tagline { color: #9a9a9a; font-size: 11px; }
  .services {
    margin-top: 58px;
    text-align: center;
    font-size: 21px;
    line-height: 1.35;
    color: var(--white);
  }
  .services .dot { font-size: 15px; vertical-align: 2px; padding: 0 4px; }
</style>
</head>
<body>

  <section class="card card-front" aria-label="Business card front">
    <div class="brand-panel">
      <div class="brand-mark"></div>
      <div class="brand-name">Stride &amp;<br>Core</div>
      <div class="brand-tagline">Personal Training. Nutrition. Motivation</div>
    </div>
    <div class="contact-panel">
      <h1 class="person-name">Marcus Reed</h1>
      <p class="person-role">Managing Director</p>
      <ul class="contact-list">
        <li>
          <svg viewBox="0 0 24 24" fill="none" stroke="#9b5bd6" stroke-width="2"><path d="M5 3h4l2 5-2.5 1.5a11 11 0 0 0 6 6L16 13l5 2v4a2 2 0 0 1-2 2A16 16 0 0 1 3 5a2 2 0 0 1 2-2z"/></svg>
          044-555 018 240
        </li>
        <li>
          <svg viewBox="0 0 24 24" fill="none" stroke="#9b5bd6" stroke-width="2"><rect x="3" y="5" width="18" height="14" rx="1"/><path d="M3 6l9 7 9-7"/></svg>
          info@strideandcore.com
        </li>
        <li>
          <svg viewBox="0 0 24 24" fill="none" stroke="#9b5bd6" stroke-width="2"><circle cx="12" cy="12" r="9"/><path d="M3 12h18M12 3c3 3 3 15 0 18M12 3c-3 3-3 15 0 18"/></svg>
          <span>www.<span class="accent">strideandcore</span>.com</span>
        </li>
      </ul>
      <p class="address">88, Harbour Lane, Westbrook<br>60318, Country Name</p>
    </div>
  </section>

  <section class="card card-back" aria-label="Business card back">
    <div class="back-brand">
      <div class="brand-mark"></div>
      <div class="brand-text">
        <div class="brand-name">Stride &amp; Core</div>
        <div class="brand-tagline">Personal Training. Nutrition. Motivation</div>
      </div>
    </div>
    <p class="services">
      Weight loss &amp; Conditioning <span class="dot">●</span> Strength Training<br>
      Muscle Gain <span class="dot">●</span> Strength Endurance
    </p>
  </section>

</body>
</html>
```